I need a business card design for a real estate finance, development and management business. We deal with high net worth clients and ask that the business card be neat, clean and sophisticated. We like the attached logo design, font and color and want to incorporate all this into the business card.

Industry/Entity Type

Real Estate

```html
<!DOCTYPE html>
<html lang="en">
<head>
<meta charset="utf-8">
<title>Silver Harbor – Business Card</title>
<link rel="stylesheet" href="https://fonts.googleapis.com/css2?family=Open+Sans:wght@400;600;700&display=swap">
<style>
  :root {
    --brand-blue: #21609d;
    --paper: #ffffff;
    --backdrop: #e6e6e8;
    --ink-light: #ffffff;
  }
  * { box-sizing: border-box; margin: 0; padding: 0; }
  html, body {
    width: 1200px; height: 947px; overflow: hidden;
    background: var(--backdrop);
    font-family: "Open Sans", Arial, sans-serif;
  }
  .stage {
    position: relative; width: 1200px; height: 947px;
    display: flex; align-items: center; justify-content: center; gap: 60px;
  }
  .card {
    position: relative; width: 520px; height: 297px; overflow: hidden;
    box-shadow: 0 2px 6px rgba(0,0,0,0.12);
  }

  /* Logo side */
  .card--logo { background: var(--paper); }
  .card--logo .edge {
    position: absolute; left: 0; right: 0; height: 18px; background: var(--brand-blue);
  }
  .card--logo .edge--top { top: 0; }
  .card--logo .edge--bottom { bottom: 0; }

  .wordmark {
    position: absolute; left: 0; right: 0; text-align: center;
    font-family: "Open Sans", Arial, sans-serif;
    font-weight: 600; letter-spacing: 3px; text-transform: uppercase; line-height: 1;
  }
  .card--logo .wordmark { top: 130px; font-size: 34px; color: var(--brand-blue); }

  /* Contact side */
  .card--contact { background: var(--brand-blue); color: var(--ink-light); }
  .card--contact .wordmark { top: 44px; left: 40px; font-size: 27px; color: var(--ink-light); }

  .name-band {
    position: absolute; left: 0; right: 0; top: 118px; height: 52px;
    background: var(--paper); color: var(--brand-blue);
    display: flex; align-items: center; justify-content: space-between;
    padding: 0 20px;
  }
  .mobile { display: flex; align-items: center; gap: 10px; font-size: 13px; }
  .mobile__icon {
    width: 22px; height: 22px; background: var(--brand-blue); border-radius: 3px;
    display: flex; align-items: center; justify-content: center;
  }
  .person { font-size: 17px; font-weight: 400; letter-spacing: 0.5px; }
  .person strong { font-weight: 700; }

  .details {
    position: absolute; left: 20px; right: 20px; top: 188px;
    display: grid; grid-template-columns: 1.15fr 1fr 1.25fr; gap: 14px;
    font-size: 12.5px; line-height: 1.35;
  }
  .detail__icon { display: block; margin-bottom: 5px; }
  .details .detail:nth-child(2) { padding-left: 10px; }
</style>
</head>
<body>
<main class="stage">

  <section class="card card--logo" aria-label="Business card, logo side">
    <div class="edge edge--top"></div>
    <div class="wordmark">Silver Harbor</div>
    <div class="edge edge--bottom"></div>
  </section>

  <section class="card card--contact" aria-label="Business card, contact side">
    <div class="wordmark">Silver Harbor</div>

    <div class="name-band">
      <div class="mobile">
        <span class="mobile__icon">
          <svg width="10" height="15" viewBox="0 0 10 15" aria-hidden="true">
            <rect x="0.8" y="0.8" width="8.4" height="13.4" rx="1.4" fill="none" stroke="#fff" stroke-width="1.4"/>
            <circle cx="5" cy="11.8" r="0.9" fill="#fff"/>
          </svg>
        </span>
        <span>+0000 1234 5679</span>
      </div>
      <div class="person">YOUR<strong>NAME</strong></div>
    </div>

    <div class="details">
      <div class="detail">
        <svg class="detail__icon" width="14" height="13" viewBox="0 0 14 13" aria-hidden="true">
          <path d="M7 0.5 L13.5 6.5 H11.5 V12.5 H8.5 V8.5 H5.5 V12.5 H2.5 V6.5 H0.5 Z" fill="#fff"/>
        </svg>
        Your Local or business address.
      </div>
      <div class="detail">
        <svg class="detail__icon" width="15" height="13" viewBox="0 0 15 13" aria-hidden="true">
          <path d="M1 4 Q7.5 -0.5 14 4 L12.5 5.5 L10.5 4.5 V3.5 Q7.5 2.5 4.5 3.5 V4.5 L2.5 5.5 Z" fill="#fff"/>
          <path d="M3.5 6.5 H11.5 L13 12.5 H2 Z" fill="#fff"/>
          <circle cx="7.5" cy="9.3" r="1.5" fill="#21609d"/>
        </svg>
        +000 1234 5679<br>+000 1234 5679
      </div>
      <div class="detail">
        <svg class="detail__icon" width="15" height="13" viewBox="0 0 15 13" aria-hidden="true">
          <rect x="0.5" y="0.5" width="14" height="9" rx="1" fill="#fff"/>
          <rect x="5.5" y="10" width="4" height="1.5" fill="#fff"/>
          <rect x="3.5" y="11.5" width="8" height="1.2" fill="#fff"/>
        </svg>
        name@yourwebsite.com<br>www.yourwebsite.com
      </div>
    </div>
  </section>

</main>
</body>
</html>
```